Bright Harbor Web Design & Marketing

Will award a 2nd place prize of $100.00 if someone can come up with a logo to match this design!
Updates

Okay, I'm really looking to see some better designs here. What do you think will bring the best designs out? Please remember with all future submissions I'm looking for a cartoon style / illustrator style website. I'm not sure what the technical term is for it, so I uploaded some images in the brief.

Target Market(s)

Small Business Owners

Industry/Entity Type

Marketing

Logo Text

BrightHarbor.com

Number of Pages Required

1 page

Colors

Designer to choose colors to be used in the design.

Requirements
Must have
• Logo should say BrightHarbor.com I would like more than just a text logo. I want some sort of cool custom graphic / icon with it that will look nice on shirts/hats/etc

```html
<!DOCTYPE html>
<html lang="en">
<head>
<meta charset="utf-8">
<title>Bright Harbor Web Design &amp; Marketing</title>
<link href="https://fonts.googleapis.com/css2?family=Cinzel:wght@400;700&family=Open+Sans:wght@400;600;700&family=Roboto:wght@500;700&display=swap" rel="stylesheet">
<style>
:root{
  --teal:#2fc3cf;
  --teal-deep:#1ea9b8;
  --ink:#1c1c1c;
  --text:#555;
  --grey-btn:#5e5e5e;
  --navy:#0f1a2b;
  --blue:#2f7ec7;
  --blue-deep:#2563a8;
  --cream:#f6f3ec;
  --light:#f3f3f3;
  --orange:#f08a24;
  --sky:#5fd4ff;
  --white:#fff;
}
*{box-sizing:border-box;margin:0;padding:0}
html,body{width:1200px;height:4737px;overflow:hidden}
body{font-family:"Open Sans",Arial,sans-serif;color:var(--text);background:var(--white);font-size:13px;line-height:1.55}
section,header,footer{position:relative;width:1200px;overflow:hidden}
.abs{position:absolute}
.section-title{font-family:"Cinzel",Georgia,serif;font-size:30px;color:var(--ink);text-align:center;letter-spacing:1px;font-weight:400}
.section-lead{width:900px;margin:0 auto;text-align:center;font-size:12.5px;line-height:1.6}
.btn{display:inline-flex;align-items:center;justify-content:center;gap:8px;color:var(--white);font-size:14px;border-radius:3px}

/* hero */
.hero{height:594px;background:linear-gradient(180deg,#45d3dc 0%,#2fc1cd 100%)}
.hero-art{left:40px;top:120px;width:470px;height:420px;border-radius:20px;background:radial-gradient(circle at 45% 50%,rgba(255,255,255,.35),rgba(255,255,255,.05) 70%)}
.topbar{left:0;top:0;width:1200px;height:58px;background:rgba(12,30,40,.55)}
.logo{left:142px;top:0;width:158px;height:142px;background:var(--white);display:flex;flex-direction:column;align-items:center;justify-content:center;box-shadow:0 2px 6px rgba(0,0,0,.2)}
.logo-mark{width:46px;height:46px;border-radius:50%;background:var(--teal);margin-bottom:8px}
.logo-name{font-family:"Roboto",Arial,sans-serif;font-weight:700;font-size:17px;color:var(--blue-deep)}
.nav{right:110px;top:0;height:58px;display:flex;gap:36px;align-items:center}
.nav a{color:var(--white);text-decoration:none;font-size:12.5px;font-weight:600;letter-spacing:.5px;position:relative}
.nav a.active::after{content:"";position:absolute;left:0;right:0;bottom:-8px;height:2px;background:var(--white)}
.hero-head{left:552px;top:215px;width:560px;font-family:"Roboto",Arial,sans-serif;font-weight:700;font-size:44px;line-height:1.2;color:var(--ink);text-align:right}
.hero-head .w{color:var(--white)}
.hero-call{left:890px;top:461px;width:164px;height:41px;background:var(--grey-btn)}
.slide-arrow{top:350px;width:24px;height:28px;background:rgba(0,0,0,.55);display:flex;align-items:center;justify-content:center}

/* about */
.about{height:322px;padding-top:60px}
.about .section-title span{color:var(--teal-deep)}
.about .section-lead{margin-top:22px;width:960px}
.about-btns{display:flex;justify-content:center;gap:16px;margin-top:30px}
.btn-read{width:128px;height:38px;background:var(--teal)}
.btn-call{width:150px;height:38px;background:var(--grey-btn)}

/* services */
.services{height:758px;background:linear-gradient(180deg,#1b2330 0%,#151b25 60%,#1e2a2f 100%)}
.services-scene{left:0;top:0;width:1200px;height:758px;background:radial-gradient(ellipse at 50% 60%,rgba(70,90,110,.45),rgba(0,0,0,0) 70%)}
.services .section-title{color:var(--white);padding-top:40px}
.services .section-lead{color:#d6d6d6;margin-top:14px;width:1000px}
.svc{width:210px;font-size:10.5px;line-height:1.35;color:#cfcfcf}
.svc b{display:block;font-size:12px;font-weight:600;margin-bottom:3px}
.svc.r{text-align:right}

/* plans */
.plans{height:663px;background:var(--light)}
.plans .section-title{padding-top:52px}
.floor{left:0;top:505px;width:1200px;height:158px;background:linear-gradient(180deg,#c9a77c,#a57d52)}
.card{top:142px;width:190px;height:458px;background:var(--white);border-top:4px solid var(--orange);box-shadow:0 3px 10px rgba(0,0,0,.15);text-align:center}
.card-icon{width:54px;height:54px;border-radius:50%;background:#e8f2fb;margin:26px auto 0;display:flex;align-items:center;justify-content:center}
.card-name{font-size:15px;color:var(--ink);margin-top:16px}
.card-price{background:#f6f6f6;margin-top:16px;padding:12px 0 14px}
.card-price small{display:block;font-size:10px;color:#888}
.card-price .amt{font-size:40px;color:#333;line-height:1.1}
.card-price .amt sup{font-size:16px;vertical-align:20px}
.card-price .amt sub{font-size:14px;vertical-align:0}
.card ul{list-style:none;text-align:left;padding:14px 22px 0;font-size:11px}
.card li{padding:5px 0;border-bottom:1px solid #eee}
.card li::before{content:"› ";color:#999}
.card-go{margin:18px auto 0;width:128px;height:32px;background:#444;font-size:12px}
.card-more{font-size:10.5px;color:#666;margin-top:6px}
.card.basic .amt{color:var(--teal-deep)}
.card.basic .card-go{background:var(--teal)}

/* video */
.video{height:505px}
.video .section-title{padding-top:68px}
.hands{left:332px;top:150px;width:536px;height:355px;background:linear-gradient(180deg,rgba(240,205,180,0) 40%,#e7c1a5 100%)}
.tablet{left:426px;top:120px;width:402px;height:306px;border-radius:24px;background:#f8f8f8;border:2px solid #ddd;box-shadow:0 4px 14px rgba(0,0,0,.15)}
.tablet-screen{left:44px;top:24px;width:310px;height:256px;background:linear-gradient(160deg,#5b5a8f,#3d3a6d);display:flex;align-items:center;justify-content:center}
.tablet-brand{position:absolute;top:56px;left:0;right:0;text-align:center;font-family:"Roboto",Arial,sans-serif;font-weight:700;font-size:18px;color:var(--white)}
.video-link{left:0;width:1200px;top:442px;text-align:center;color:#c0392b;font-size:13px;text-decoration:underline}

/* band */
.band{height:95px;background:var(--blue);display:flex;align-items:center;justify-content:center;text-align:center;font-family:"Cinzel",Georgia,serif;color:var(--white);font-size:16px;line-height:1.55;letter-spacing:.5px}

/* clients */
.clients{height:253px;background:var(--cream)}
.clients .section-title{padding-top:34px}
.clients .section-lead{margin-top:16px}
.client-row{left:110px;top:170px;width:980px;display:flex;justify-content:space-between;align-items:center}
.client{display:flex;align-items:center;gap:6px;font-family:"Open Sans",Arial,sans-serif;font-weight:700;font-size:14px;color:#333}
.client i{width:14px;height:14px;border-radius:50%;background:#333;display:block}
.arrow-s{width:14px;color:#777;font-size:20px}

/* why */
.why{height:410px;background:linear-gradient(180deg,#1f2e22 0%,#2c3d27 50%,#1c2519 100%)}
.why-scene{left:0;top:0;width:1200px;height:410px;background:radial-gradient(ellipse at 30% 70%,rgba(140,50,50,.25),rgba(0,0,0,0) 60%)}
.why .section-title{color:var(--white);padding-top:56px}
.why .section-lead{color:#dcdcdc;margin-top:10px;width:980px}
.why-item{width:230px;font-size:11px;color:#e4e4e4;line-height:1.35}
.why-item b{display:block;color:var(--sky);font-weight:600;font-size:12px}
.why-item.r{text-align:right}

/* team */
.team{height:458px}
.team .section-title{padding-top:68px}
.team .section-lead{margin-top:14px}
.member{top:258px;width:460px;height:148px;border:1px solid #e6e6e6;background:var(--white);padding:20px}
.member-photo{left:20px;top:16px;width:62px;height:62px;background:linear-gradient(160deg,#b8c3cc,#6c7a86)}
.member-name{left:100px;top:24px;color:var(--blue-deep);font-weight:600;font-size:12.5px}
.member-role{left:100px;top:42px;color:#888;font-size:11px}
.member-text{left:20px;top:88px;width:420px;font-size:11px;line-height:1.5}
.team-arrow{top:320px;color:#999;font-size:26px}

/* inquiry */
.inquiry{height:395px;background:#fafafa}
.desk{left:0;top:47px;width:474px;height:348px;background:linear-gradient(120deg,#e9ecef 0%,#cfd5db 60%,#f4f6f7 100%)}
.inquiry .section-title{position:absolute;left:490px;width:536px;top:50px}
.form{left:490px;top:110px;width:536px}
.field{position:absolute;height:34px;border-bottom:1px solid #cfcfcf;font-size:11px;color:#888;padding-top:6px}
.field.area{height:72px;border:1px solid #cfcfcf;padding:6px}
.submit{position:absolute;left:0;top:216px;width:80px;height:28px;background:var(--blue);font-size:11px}

/* footer */
.footer{height:252px;background:linear-gradient(180deg,#101a2c 0%,#1b2942 100%)}
.skyline{left:0;top:110px;width:1200px;height:142px;background:linear-gradient(180deg,rgba(60,80,110,0),rgba(60,80,110,.55))}
.fcol{top:32px;color:#cdd4de;font-size:11px;line-height:1.6}
.fcol h4{font-family:"Open Sans",Arial,sans-serif;font-size:13px;font-weight:600;color:var(--white);margin-bottom:8px}
.fcol h4 span{color:var(--orange)}
.fcol ul{list-style:none}
.fcol li::before{content:"› ";color:var(--orange)}
.contact-line{display:flex;align-items:center;gap:6px}
.contact-line i{width:16px;height:16px;border-radius:50%;background:var(--blue);display:flex;align-items:center;justify-content:center}
.news-input{width:200px;height:24px;background:var(--white);margin-top:12px;color:#888;padding:3px 6px}
.news-btn{margin-top:8px;width:110px;height:26px;background:var(--blue);font-size:11px}
.footer-art{left:916px;top:40px;width:220px;height:170px;background:radial-gradient(circle,rgba(200,200,200,.25),rgba(0,0,0,0) 70%)}
.bottombar{height:32px;background:var(--blue-deep);color:var(--white);font-size:11px;display:flex;justify-content:space-between;align-items:center;padding:0 142px}
</style>
</head>
<body>

<header class="hero">
  <div class="abs hero-art" role="img" aria-label="Illustration of a rising growth chart with charts, gears and a cloud"></div>
  <div class="abs topbar"></div>
  <div class="abs logo">
    <div class="logo-mark"></div>
    <div class="logo-name">BrightHarbor.com</div>
  </div>
  <nav class="abs nav">
    <a class="active" href="#">HOME</a>
    <a href="#">SERVICES &amp; PRICING</a>
    <a href="#">OUR TEAM</a>
    <a href="#">CLIENTS</a>
    <a href="#">CONTACT US</a>
  </nav>
  <h1 class="abs hero-head">The Design &amp; Marketing<br>Team <span class="w">That Always Puts</span><br><span class="w">Honesty &amp; Care</span> Before<br>Profits</h1>
  <div class="abs btn hero-call">
    <svg width="14" height="14" viewBox="0 0 24 24"><path fill="#fff" d="M6.6 10.8a15 15 0 0 0 6.6 6.6l2.2-2.2c.3-.3.7-.4 1-.2 1.1.4 2.3.6 3.6.6.6 0 1 .4 1 1V20c0 .6-.4 1-1 1A17 17 0 0 1 3 4c0-.6.4-1 1-1h3.5c.6 0 1 .4 1 1 0 1.3.2 2.5.6 3.6.1.3 0 .7-.2 1z"/></svg>
    Call Us Today
  </div>
  <div class="abs slide-arrow" style="left:6px"><svg width="10" height="12" viewBox="0 0 10 12"><path d="M8 0 0 6l8 6z" fill="#fff"/></svg></div>
  <div class="abs slide-arrow" style="right:6px"><svg width="10" height="12" viewBox="0 0 10 12"><path d="M2 0l8 6-8 6z" fill="#fff"/></svg></div>
</header>

<section class="about">
  <h2 class="section-title">About <span>BrightHarbor</span><small style="font-size:14px;color:var(--teal-deep)">.com</small></h2>
  <p class="section-lead">We believe that honesty and integrity come before personal profits. We are a family owned and operated company. Our parents raised us to take care of each other and that is exactly what we have done. We treat each of our clients with the same loyalty and respect that we give each other.<br>We are not looking to have hundreds and hundreds of clients. We are looking to expand our family with a handful of like-minded individuals. Companies who take pride in their work, and their customers. We want to build mutually beneficial, lucrative, and long term partnerships.</p>
  <div class="about-btns">
    <div class="btn btn-read">
      <svg width="14" height="14" viewBox="0 0 24 24"><path fill="#fff" d="M4 11h12l-4-4 1.4-1.4L20 12l-6.6 6.4L12 17l4-4H4z"/></svg>Read More</div>
    <div class="btn btn-call">
      <svg width="14" height="14" viewBox="0 0 24 24"><path fill="#fff" d="M6.6 10.8a15 15 0 0 0 6.6 6.6l2.2-2.2c.3-.3.7-.4 1-.2 1.1.4 2.3.6 3.6.6.6 0 1 .4 1 1V20c0 .6-.4 1-1 1A17 17 0 0 1 3 4c0-.6.4-1 1-1h3.5c.6 0 1 .4 1 1 0 1.3.2 2.5.6 3.6.1.3 0 .7-.2 1z"/></svg>Call Us Today</div>
  </div>
</section>

<section class="services">
  <div class="abs services-scene" role="img" aria-label="Cartoon street scene with a small business team at work"></div>
  <h2 class="section-title">Services We Provide</h2>
  <p class="section-lead">Lorem ipsum dolor sit amet, consectetuer adipiscing elit, sed diam nonummy nibh euismod tincidunt ut laoreet dolore magna aliquam erat volutpat. Ut wisi enim ad minim veniam, quis nostrud exerci.</p>
  <svg class="abs" style="left:0;top:0" width="1200" height="758" viewBox="0 0 1200 758">
    <circle cx="600" cy="410" r="210" fill="none" stroke="#3a4a5e" stroke-width="3" stroke-dasharray="6 6"/>
    <circle cx="600" cy="410" r="130" fill="#2a3647" role="img" aria-label="Illustration of a team working together"/>
    <g font-family="Roboto, Arial, sans-serif" font-size="20" font-weight="700" fill="#fff" text-anchor="middle">
      <circle cx="528" cy="213" r="30" fill="#f4b41a"/><text x="528" y="220">1</text>
      <circle cx="672" cy="213" r="30" fill="#1fb6d9"/><text x="672" y="220">2</text>
      <circle cx="782" cy="305" r="30" fill="#7cc242"/><text x="782" y="312">3</text>
      <circle cx="807" cy="446" r="30" fill="#9b3fbf"/><text x="807" y="453">4</text>
      <circle cx="735" cy="571" r="30" fill="#e0402d"/><text x="735" y="578">5</text>
      <circle cx="600" cy="620" r="30" fill="#2f7ec7"/><text x="600" y="627">6</text>
      <circle cx="465" cy="571" r="30" fill="#1fb6d9"/><text x="465" y="578">7</text>
      <circle cx="393" cy="446" r="30" fill="#f08a24"/><text x="393" y="453">8</text>
      <circle cx="418" cy="305" r="30" fill="#17a88f"/><text x="418" y="312">9</text>
    </g>
  </svg>
  <div class="abs svc r" style="left:285px;top:160px"><b style="color:#f4b41a">Consulting Service</b>Duis autem vel eum iriure dolor in hendrerit in vulputate velit consequat.</div>
  <div class="abs svc" style="left:712px;top:160px"><b style="color:#1fb6d9">Website Design &amp; Management</b>Duis autem vel eum iriure dolor in hendrerit in vulputate velit consequat.</div>
  <div class="abs svc" style="left:822px;top:260px"><b style="color:#7cc242">Logo Design &amp; Branding Materials</b>Duis autem vel eum iriure dolor in hendrerit in vulputate velit consequat.</div>
  <div class="abs svc" style="left:847px;top:410px"><b style="color:#b65ad6">Online Reputation Management</b>Duis autem vel eum iriure dolor in hendrerit in vulputate velit consequat.</div>
  <div class="abs svc" style="left:775px;top:540px"><b style="color:#e0402d">Local Seo Management</b>Duis autem vel eum iriure dolor in hendrerit in vulputate velit consequat.</div>
  <div class="abs svc" style="left:640px;top:655px"><b style="color:#4aa3ec">Search Engine Optimization</b>Duis autem vel eum iriure dolor in hendrerit in vulputate velit consequat.</div>
  <div class="abs svc r" style="left:215px;top:560px"><b style="color:#1fb6d9">Social Media Marketing</b>Duis autem vel eum iriure dolor in hendrerit in vulputate velit consequat.</div>
  <div class="abs svc r" style="left:143px;top:420px"><b style="color:#f08a24">Marketing Material &amp; Print Design</b>Duis autem vel eum iriure dolor in hendrerit in vulputate velit consequat.</div>
  <div class="abs svc r" style="left:168px;top:270px"><b style="color:#17a88f">Ecommerce Management</b>Duis autem vel eum iriure dolor in hendrerit in vulputate velit consequat.</div>
</section>

<section class="plans">
  <div class="abs floor" role="img" aria-label="Wooden floor boards"></div>
  <h2 class="section-title">Select Your Plan</h2>

  <div class="abs card basic" style="left:158px">
    <div class="card-icon"><svg width="22" height="22" viewBox="0 0 24 24"><path fill="#2f7ec7" d="M4 20 14 10l2 2L6 22H4zM15 9l3-3 2 2-3 3z"/></svg></div>
    <div class="card-name">Basic Plan</div>
    <div class="card-price"><small>Starting from</small><div class="amt"><sup>$</sup>52<sub>.95</sub></div></div>
    <ul><li>Lorem Ipsum Dolar Sapien</li><li>Lorem Ipsum Dolar</li><li>Lorem Ipsum Dolar Sapien</li><li>Lorem Ipsum Dolar</li></ul>
    <div class="btn card-go">Get Started →</div>
    <div class="card-more">More Information</div>
  </div>
  <div class="abs card" style="left:395px">
    <div class="card-icon"><svg width="22" height="22" viewBox="0 0 24 24"><rect x="3" y="5" width="18" height="12" rx="1" fill="none" stroke="#2f7ec7" stroke-width="2"/><path d="M8 20h8" stroke="#2f7ec7" stroke-width="2"/></svg></div>
    <div class="card-name">Standard Plan</div>
    <div class="card-price"><small>Starting from</small><div class="amt"><sup>$</sup>114<sub>.00</sub></div></div>
    <ul><li>Lorem Ipsum Dolar Sapien</li><li>Lorem Ipsum Dolar</li><li>Lorem Ipsum Dolar Sapien</li><li>Lorem Ipsum Dolar</li></ul>
    <div class="btn card-go">Get Started →</div>
    <div class="card-more">More Information</div>
  </div>
  <div class="abs card" style="left:625px">
    <div class="card-icon"><svg width="22" height="22" viewBox="0 0 24 24"><circle cx="12" cy="12" r="8" fill="none" stroke="#2f7ec7" stroke-width="2"/><path d="M12 7v5l3 3" stroke="#2f7ec7" stroke-width="2" fill="none"/></svg></div>
    <div class="card-name">Gold Plan</div>
    <div class="card-price"><small>Starting from</small><div class="amt"><sup>$</sup>200<sub>.95</sub></div></div>
    <ul><li>Lorem Ipsum Dolar Sapien</li><li>Lorem Ipsum Dolar</li><li>Lorem Ipsum Dolar Sapien</li><li>Lorem Ipsum Dolar</li></ul>
    <div class="btn card-go">Get Started →</div>
    <div class="card-more">More Information</div>
  </div>
  <div class="abs card" style="left:853px">
    <div class="card-icon"><svg width="22" height="22" viewBox="0 0 24 24"><circle cx="10" cy="10" r="6" fill="none" stroke="#2f7ec7" stroke-width="2"/><path d="M15 15l5 5" stroke="#2f7ec7" stroke-width="2"/></svg></div>
    <div class="card-name">Platinum Plan</div>
    <div class="card-price"><small>Starting from</small><div class="amt"><sup>$</sup>490<sub>.00</sub></div></div>
    <ul><li>Lorem Ipsum Dolar Sapien</li><li>Lorem Ipsum Dolar</li><li>Lorem Ipsum Dolar Sapien</li><li>Lorem Ipsum Dolar</li></ul>
    <div class="btn card-go">Get Started →</div>
    <div class="card-more">More Information</div>
  </div>
</section>

<section class="video">
  <h2 class="section-title">Watch Video</h2>
  <div class="abs hands" role="img" aria-label="Two hands holding a tablet"></div>
  <div class="abs tablet">
    <div class="abs tablet-screen">
      <div class="tablet-brand">BrightHarbor.com</div>
      <svg width="60" height="60" viewBox="0 0 60 60"><circle cx="30" cy="30" r="28" fill="#fff"/><path d="M24 18l18 12-18 12z" fill="#3d3a6d"/></svg>
    </div>
  </div>
  <div class="abs video-link">View Video</div>
</section>

<div class="band">Lorem ipsum dolor sit amet, consectetuer adipiscing elit, sed diam nonummy nibh<br>euismod tincidunt ut laoreet dolore magna aliquam erat volutpat</div>

<section class="clients">
  <h2 class="section-title">Our Clients</h2>
  <p class="section-lead">Lorem ipsum dolor sit amet, consectetuer adipiscing elit, sed diam nonummy nibh euismod tincidunt ut laoreet dolore magna aliquam erat volutpat. Ut wisi enim ad minim veniam, quis nostrud exerci.</p>
  <div class="abs client-row">
    <span class="arrow-s">‹</span>
    <span class="client"><i></i>Linden Row</span>
    <span class="client"><i></i>Northvale</span>
    <span class="client"><i></i>Northvale</span>
    <span class="client"><i></i>Quartzline</span>
    <span class="client"><i></i>Linden Row</span>
    <span class="client"><i></i>Meridia</span>
    <span class="client"><i></i>Stoneworks</span>
    <span class="client"><i></i>Stoneworks</span>
    <span class="arrow-s">›</span>
  </div>
</section>

<section class="why">
  <div class="abs why-scene" role="img" aria-label="Dark garden foliage with red flowers"></div>
  <h2 class="section-title">Why Choose Us</h2>
  <p class="section-lead">Lorem ipsum dolor sit amet, consectetuer adipiscing elit, sed diam nonummy nibh euismod tincidunt ut laoreet dolore magna aliquam erat volutpat. Ut wisi enim ad minim veniam, quis nostrud exerci.</p>
  <svg class="abs" style="left:0;top:0" width="1200" height="410" viewBox="0 0 1200 410">
    <circle cx="600" cy="240" r="95" fill="none" stroke="#5fd4ff" stroke-width="2" stroke-dasharray="4 6"/>
    <circle cx="600" cy="240" r="62" fill="rgba(255,255,255,.12)" role="img" aria-label="Illustration of two people shaking hands"/>
    <g fill="#2f7ec7" stroke="#fff" stroke-width="2">
      <circle cx="512" cy="205" r="15"/><circle cx="688" cy="205" r="15"/>
      <circle cx="510" cy="278" r="15"/><circle cx="690" cy="278" r="15"/>
      <circle cx="600" cy="335" r="15"/>
    </g>
  </svg>
  <div class="abs why-item r" style="left:266px;top:186px"><b>100% Risk Free Investment</b>Lorem ipsum dolor sit amet, consectetuer adipiscing elit.</div>
  <div class="abs why-item" style="left:706px;top:186px"><b>Multiple Payment Options Available</b>Lorem ipsum dolor sit amet, consectetuer adipiscing elit.</div>
  <div class="abs why-item r" style="left:264px;top:259px"><b>Experienced Qualified Designers</b>Lorem ipsum dolor sit amet, consectetuer adipiscing elit.</div>
  <div class="abs why-item" style="left:708px;top:259px"><b>Unmatched Personal Service</b>Lorem ipsum dolor sit amet, consectetuer adipiscing elit.</div>
  <div class="abs why-item" style="left:485px;top:354px;text-align:center;width:230px"><b>24/7/365 Email Customer Support</b>Lorem ipsum dolor sit amet, elit.</div>
</section>

<section class="team">
  <h2 class="section-title">Our Team</h2>
  <p class="section-lead">Lorem ipsum dolor sit amet, consectetuer adipiscing elit, sed diam nonummy nibh euismod tincidunt ut laoreet dolore magna aliquam erat volutpat. Ut wisi enim ad minim veniam, quis nostrud exerci.</p>
  <div class="abs team-arrow" style="left:110px">‹</div>
  <div class="abs member" style="left:142px">
    <div class="abs member-photo" role="img" aria-label="Portrait photo of the chief executive officer"></div>
    <div class="abs member-name">DANIEL ASHCOMBE</div>
    <div class="abs member-role">Chief Executive Officer</div>
    <p class="abs member-text">Lorem ipsum dolor sit amet, consectetuer adipiscing elit, sed diam nonummy nibh euismod tincidunt ut laoreet dolore magna aliquam... [+]</p>
  </div>
  <div class="abs member" style="left:630px">
    <div class="abs member-photo" role="img" aria-label="Portrait photo of the chief operations officer"></div>
    <div class="abs member-name">OWEN PELLHAM</div>
    <div class="abs member-role">Chief Operations Officer</div>
    <p class="abs member-text">Lorem ipsum dolor sit amet, consectetuer adipiscing elit, sed diam nonummy nibh euismod tincidunt ut laoreet dolore magna aliquam... [+]</p>
  </div>
  <div class="abs team-arrow" style="left:1100px">›</div>
</section>

<section class="inquiry">
  <div class="abs desk" role="img" aria-label="Photo of hands typing on a laptop at a white desk"></div>
  <h2 class="section-title">Quick Inquiry</h2>
  <form class="abs form">
    <div class="field" style="left:0;top:0;width:258px">First Name</div>
    <div class="field" style="left:278px;top:0;width:258px">Last Name</div>
    <div class="field" style="left:0;top:44px;width:258px">Email</div>
    <div class="field" style="left:278px;top:44px;width:258px">Phone Number</div>
    <div class="field" style="left:0;top:88px;width:536px;border:none">Details About Your Enquiry</div>
    <div class="field area" style="left:0;top:118px;width:536px"></div>
    <div class="btn submit">SUBMIT</div>
  </form>
</section>

<footer class="footer">
  <div class="abs skyline" role="img" aria-label="Night city skyline"></div>
  <div class="abs fcol" style="left:142px">
    <h4>Quick <span>Links</span></h4>
    <ul><li>Home</li><li>Services</li><li>Pricing</li><li>Our Team</li><li>Support/Notes</li><li>Clients</li><li>Contact Us</li></ul>
  </div>
  <div class="abs fcol" style="left:332px">
    <h4>Contact <span>Details</span></h4>
    <div style="color:#fff;font-weight:600">BrightHarbor.com</div>
    <div>120 Harbor Lane, Portview,</div>
    <div>ST 00000</div>
    <div class="contact-line" style="margin-top:6px"><i><svg width="8" height="8" viewBox="0 0 24 24"><path fill="#fff" d="M6.6 10.8a15 15 0 0 0 6.6 6.6l2.2-2.2c.3-.3.7-.4 1-.2 1.1.4 2.3.6 3.6.6.6 0 1 .4 1 1V20c0 .6-.4 1-1 1A17 17 0 0 1 3 4c0-.6.4-1 1-1h3.5c.6 0 1 .4 1 1 0 1.3.2 2.5.6 3.6.1.3 0 .7-.2 1z"/></svg></i>(555) 014-2200</div>
    <div class="contact-line"><i><svg width="8" height="8" viewBox="0 0 24 24"><path fill="#fff" d="M6.6 10.8a15 15 0 0 0 6.6 6.6l2.2-2.2c.3-.3.7-.4 1-.2 1.1.4 2.3.6 3.6.6.6 0 1 .4 1 1V20c0 .6-.4 1-1 1A17 17 0 0 1 3 4c0-.6.4-1 1-1h3.5c.6 0 1 .4 1 1 0 1.3.2 2.5.6 3.6.1.3 0 .7-.2 1z"/></svg></i>(555) 014-2201</div>
    <div class="contact-line"><i><svg width="8" height="8" viewBox="0 0 24 24"><path fill="#fff" d="M2 5h20v14H2zm2 2v1l8 5 8-5V7z"/></svg></i>hello@brightharbor.com</div>
  </div>
  <div class="abs fcol" style="left:594px">
    <h4>Newsletter <span>Signup</span></h4>
    <div style="width:220px">Lorem ipsum dolor sit amet, consectetuer adipiscing elit, sed diam.</div>
    <div class="news-input">Email</div>
    <div class="btn news-btn">Subscribe</div>
  </div>
  <div class="abs footer-art" role="img" aria-label="Illustration of two people shaking hands"></div>
</footer>
<div class="bottombar"><span>Copyright © 2017 BrightHarbor.com . All rights reserved</span><span>Terms of Use | Privacy Policy</span></div>

</body>
</html>
```